Veldmark Supplies Business Card

Professional business card that stand out to our potential customers. Front and back with clean modern design

Industry/Entity Type

Oil and gas

Contact Information for Business Card

Name, address, website , office phone and cell number

Requirements
Must have
• Editable files for each employee

```html
<!DOCTYPE html>
<html lang="en">
<head>
<meta charset="utf-8">
<title>Veldmark Supplies Business Card</title>
<link rel="stylesheet" href="https://fonts.googleapis.com/css2?family=Roboto:wght@400;500;700&display=swap">
<style>
  :root {
    --backdrop: #2b2b2d;
    --card: #222224;
    --card-edge: #1a1a1b;
    --ink-light: #e9e9ea;
    --ink-soft: #c9c9cc;
    --accent-blue: #1ea9d6;
    --accent-red: #e5212a;
    --gloss: #3a3a3d;
  }
  * { box-sizing: border-box; margin: 0; padding: 0; }
  html, body {
    width: 1200px; height: 852px; overflow: hidden;
    background: var(--backdrop);
    font-family: "Roboto", Arial, sans-serif;
  }
  .canvas { position: relative; width: 1200px; height: 852px; }

  .card {
    position: absolute;
    width: 500px; height: 286px;
    background: var(--card);
    border-radius: 22px;
    overflow: hidden;
    box-shadow: 0 14px 30px rgba(0,0,0,0.45);
  }
  .card--front { left: 70px; top: 170px; }
  .card--back { left: 630px; top: 396px; }

  /* Front */
  .front-mark {
    position: absolute; inset: 0;
    display: flex; align-items: center; justify-content: center; gap: 14px;
  }
  .front-mark__square {
    width: 22px; height: 22px; background: var(--gloss);
  }
  .front-mark__name {
    font-weight: 700; font-size: 30px; letter-spacing: 3px;
    color: var(--gloss); text-transform: uppercase;
  }

  /* Back */
  .brand-name {
    position: absolute; left: 34px; top: 108px; width: 190px;
    font-weight: 700; font-size: 34px; line-height: 1.05;
    color: var(--accent-red);
  }
  .contact {
    position: absolute; left: 268px; top: 40px; color: var(--ink-soft);
  }
  .contact__name {
    font-weight: 500; font-size: 21px; color: var(--accent-blue);
  }
  .contact__title { font-size: 12px; color: var(--ink-light); margin-top: 3px; }
  .contact__address { font-size: 12.5px; line-height: 1.4; margin-top: 26px; }
  .contact__list { list-style: none; margin-top: 8px; font-size: 12.5px; line-height: 1.45; }
  .contact__list li { display: flex; align-items: center; gap: 8px; }
  .contact__icon { width: 11px; height: 11px; fill: var(--accent-red); flex: none; }

  .band-red {
    position: absolute; left: 0; bottom: 0; width: 100%; height: 7px;
    background: var(--accent-red);
  }
  .band-blue {
    position: absolute; right: 0; bottom: 0; width: 265px; height: 44px;
    background: var(--accent-blue);
    border-top-left-radius: 18px;
    display: flex; align-items: center; justify-content: center;
    color: #fff; font-weight: 700; font-size: 14.5px;
  }
</style>
</head>
<body>
<div class="canvas">
  <section class="card card--front" aria-label="Card front">
    <div class="front-mark">
      <span class="front-mark__square"></span>
      <span class="front-mark__name">Veldmark Supplies</span>
    </div>
  </section>

  <section class="card card--back" aria-label="Card back">
    <div class="brand-name">Veldmark Supplies</div>

    <div class="contact">
      <h1 class="contact__name">Daniel Reyes Carter</h1>
      <p class="contact__title">Managing Director</p>
      <p class="contact__address">415 Mesa Ridge Suite 7<br>Midland, TX 79701</p>
      <ul class="contact__list">
        <li>
          <svg class="contact__icon" viewBox="0 0 24 24"><path d="M6.6 10.8a15.1 15.1 0 0 0 6.6 6.6l2.2-2.2a1 1 0 0 1 1-.25 11.4 11.4 0 0 0 3.6.57 1 1 0 0 1 1 1V20a1 1 0 0 1-1 1A17 17 0 0 1 3 4a1 1 0 0 1 1-1h3.5a1 1 0 0 1 1 1c0 1.25.2 2.45.57 3.57a1 1 0 0 1-.25 1z"/></svg>
          (555)014-2283
        </li>
        <li>
          <svg class="contact__icon" viewBox="0 0 24 24"><path d="M2 5h20v14H2z M3 6l9 7 9-7" stroke="#222224" stroke-width="1.6"/></svg>
          sales@veldmarksupplies.com
        </li>
        <li>
          <svg class="contact__icon" viewBox="0 0 24 24"><circle cx="12" cy="12" r="10"/><path d="M2 12h20M12 2c3 3 3 17 0 20M12 2c-3 3-3 17 0 20" stroke="#222224" stroke-width="1.5" fill="none"/></svg>
          www.veldmarksupplies.com
        </li>
      </ul>
    </div>

    <div class="band-red"></div>
    <div class="band-blue">Veldmark Supplies LLC</div>
  </section>
</div>
</body>
</html>
```